Bloom Path! A website showcasing who I am as a person

Bloom Path started out as idea for me to better myself as a person and work on small projects that would help me grow as a person. Now I want to build a website showcasing "Bloom Path." I want the website to showcase who I am and how I have grown both professionally and personally. I can build the raw code of the website on my own but I am not really much of a designer. I am looking for a design where I can write and post blogs, articles and share my thoughts. A little about myself and the ideas and interests that I want to share
What is Bloom Path
Who I am
Background - Professional
Brand Marketing
Email Automation
Hiking
Rock Climbing
Traveling
Exercising and Transformation
"Personal Thoughts"
Hopefully this is enough information to get people started on some designs.
Work
3 page

```html
<!DOCTYPE html>
<html lang="en">
<head>
<meta charset="utf-8">
<title>Arun Mehra · Bloom Path</title>
<link href="https://fonts.googleapis.com/css2?family=Roboto+Slab:wght@300;400&family=Roboto:wght@400&display=swap" rel="stylesheet">
<style>
:root{
  --page:#f4f4f4;
  --white:#ffffff;
  --blue:#2a6ba8;
  --text:#555555;
  --muted:#8a8a8a;
  --line:#e6e6e6;
  --icon:#9a9a9a;
  --slab:"Roboto Slab","Zilla Slab","DejaVu Serif",Rockwell,Georgia,serif;
  --sans:"Roboto","Helvetica Neue",Arial,sans-serif;
}
*{box-sizing:border-box;margin:0;padding:0}
html,body{width:782px;height:1200px;overflow:hidden}
body{background:var(--page);font-family:var(--slab);color:var(--text);position:relative}
.line{display:block;white-space:nowrap}

.site-nav{position:absolute;left:0;top:0;width:166px;height:1200px;background:var(--white);border-right:1px solid var(--line)}
.brand{position:absolute;right:16px;top:18px;text-align:right}
.brand-name{font-size:19px;font-weight:400;color:var(--blue);line-height:24px;white-space:nowrap}
.brand-tag{font-size:8px;color:var(--text);margin-top:-1px}
.menu{position:absolute;top:64px;left:0;width:166px;list-style:none;border-top:1px solid var(--line)}
.menu li{height:26px;border-bottom:1px solid var(--line);font-size:7.3px;line-height:25px;padding-left:18px;color:var(--text);white-space:nowrap}
.menu li::before{content:"›";margin-right:7px;font-size:9px}
.menu li.active{color:var(--blue)}
.copyright{position:absolute;left:22px;top:1140px;font-size:7px;line-height:13.5px}
.social{position:absolute;left:22px;top:1175px;display:flex;gap:13px}
.social span{width:8px;height:8px;border-radius:50%;background:var(--icon)}

.hero{position:absolute;left:183px;top:18px;width:583px;height:234px;
  background:
    radial-gradient(ellipse 35% 30% at 55% 50%,#f6f1e4 0%,rgba(246,241,228,0) 100%),
    radial-gradient(ellipse 22% 30% at 25% 70%,rgba(120,170,210,.55) 0%,rgba(120,170,210,0) 100%),
    radial-gradient(ellipse 18% 22% at 85% 12%,rgba(200,60,60,.5) 0%,rgba(200,60,60,0) 100%),
    radial-gradient(ellipse 20% 25% at 45% 5%,rgba(100,170,70,.5) 0%,rgba(100,170,70,0) 100%),
    linear-gradient(90deg,#5c4a3c 0%,#e9e0cc 18%,#eee6d4 80%,#6a5a4a 100%)}
.hero-arrow{position:absolute;top:108px;width:16px;height:18px;background:rgba(60,60,60,.55)}
.hero-arrow.prev{left:0}.hero-arrow.next{right:0}
.hero-arrow svg{display:block;margin:5px auto}

.post{position:absolute;left:183px;width:417px;height:166px;background:var(--white)}
.post-photo{position:absolute;left:0;top:0;width:166px;height:166px}
.post-body{position:absolute;left:183px;top:20px;width:218px}
.post-title{font-size:9.4px;font-weight:300;line-height:13.8px;color:#444}
.post-meta{display:flex;justify-content:space-between;align-items:center;margin-top:9px;padding:8px 0 7px;border-top:1px solid var(--line);border-bottom:1px solid var(--line);font-size:6px;color:var(--muted);white-space:nowrap}
.post-meta span{display:flex;align-items:center;gap:3px}
.post-excerpt{margin-top:11px;font-family:var(--sans);font-size:6px;line-height:11.6px;color:var(--muted)}
.more{color:var(--blue)}

.search,.newsletter-field{position:absolute;left:610px;width:157px;height:26px;background:var(--white);border:1px solid #dcdcdc;font-size:7px;color:var(--muted);padding:0 9px;display:flex;align-items:center;justify-content:space-between}
.widget{position:absolute;left:610px;width:157px;background:var(--white)}
.widget-title{font-size:12.5px;font-weight:400;color:var(--blue);padding:9px 10px 0;height:32px;border-bottom:1px solid var(--line)}
.widget-list{list-style:none;padding:15px 10px 0}
.widget-list li{display:flex;gap:6px;height:47px}
.thumb{width:32px;height:32px;flex:none;position:relative}
.widget-list p{font-size:6.2px;line-height:10.4px;color:var(--muted);margin-top:-2px}
.play{position:absolute;left:9px;top:9px}
.newsletter-title{position:absolute;left:610px;top:942px;font-size:12.5px;font-weight:400;color:var(--blue);white-space:nowrap}
.corner{position:absolute;right:14px;bottom:10px;font-family:var(--sans);font-size:7px;color:#444}
</style>
</head>
<body>

<nav class="site-nav">
  <div class="brand">
    <div class="brand-name">Arun Mehra</div>
    <div class="brand-tag">Bloom Path</div>
  </div>
  <ul class="menu">
    <li class="active">What is Bloom Path</li>
    <li>Who I am</li>
    <li>Background - Professional</li>
    <li>Brand Marketing</li>
    <li>Email Automation</li>
    <li>Hiking</li>
    <li>Rock Climbing</li>
    <li>Traveling</li>
    <li>Exercising and Transformation</li>
    <li>"Personal Thoughts"</li>
  </ul>
  <p class="copyright">Copyright © 2017 Arun Mehra<br>All rights reserved.</p>
  <div class="social"><span></span><span></span><span></span><span></span><span></span></div>
</nav>

<section class="hero" role="img" aria-label="Team planning a marketing strategy around a table with sketches and notes">
  <div class="hero-arrow prev"><svg width="6" height="8" viewBox="0 0 6 8"><path d="M5 0L1 4l4 4" stroke="#fff" fill="none" stroke-width="1.5"/></svg></div>
  <div class="hero-arrow next"><svg width="6" height="8" viewBox="0 0 6 8"><path d="M1 0l4 4-4 4" stroke="#fff" fill="none" stroke-width="1.5"/></svg></div>
</section>

<article class="post" style="top:274px">
  <div class="post-photo" role="img" aria-label="City square lit by large advertising screens at night" style="background:linear-gradient(160deg,#b3121c 0%,#1c3f8c 45%,#2a2a3a 100%)"></div>
  <div class="post-body">
    <h2 class="post-title"><span class="line">Pellentesque cursus euismod erat vel blandit.</span><span class="line">Quisque sed dolor iaculis sem sodales congue ut</span></h2>
    <div class="post-meta"><span>2 May, 2017</span><span>● 28 Comments</span><span>♥ 18 Likes</span><span>&lt; Share</span></div>
    <p class="post-excerpt"><span class="line">Mauris sed nibh congue, commodo lorem a, vehicula nulla. Pellen-</span><span class="line">tesque ullamcorper metus sed lorem ultrices tristique. Quisque</span><span class="line">vitae massa luctus ligula congue aliquam. In sagittis, velit ut malesua-</span><span class="line">da feugiat, quam diam bibendum sem, vel tempor lectus est quis</span><span class="line">quam. Nam laoreet purus ut sollicitudin semper. <span class="more">More</span></span></p>
  </div>
</article>

<article class="post" style="top:456px">
  <div class="post-photo" role="img" aria-label="Person working at a desktop computer in a bright office" style="background:linear-gradient(160deg,#cfd6da 0%,#f1f1ef 50%,#9aa3a6 100%)"></div>
  <div class="post-body">
    <h2 class="post-title"><span class="line">Pellentesque cursus euismod erat vel blandit.</span><span class="line">Quisque sed dolor iaculis sem sodales congue ut</span></h2>
    <div class="post-meta"><span>2 May, 2017</span><span>● 28 Comments</span><span>♥ 18 Likes</span><span>&lt; Share</span></div>
    <p class="post-excerpt"><span class="line">Mauris sed nibh congue, commodo lorem a, vehicula nulla. Pellen-</span><span class="line">tesque ullamcorper metus sed lorem ultrices tristique. Quisque</span><span class="line">vitae massa luctus ligula congue aliquam. In sagittis, velit ut malesua-</span><span class="line">da feugiat, quam diam bibendum sem, vel tempor lectus est quis</span><span class="line">quam. Nam laoreet purus ut sollicitudin semper. <span class="more">More</span></span></p>
  </div>
</article>

<article class="post" style="top:638px">
  <div class="post-photo" role="img" aria-label="Colleagues reviewing papers around a wooden table" style="background:linear-gradient(170deg,#d9c4a8 0%,#8a5a36 55%,#5e3a22 100%)"></div>
  <div class="post-body">
    <h2 class="post-title"><span class="line">Pellentesque cursus euismod erat vel blandit.</span><span class="line">Quisque sed dolor iaculis sem sodales congue ut</span></h2>
    <div class="post-meta"><span>2 May, 2017</span><span>● 28 Comments</span><span>♥ 18 Likes</span><span>&lt; Share</span></div>
    <p class="post-excerpt"><span class="line">Mauris sed nibh congue, commodo lorem a, vehicula nulla. Pellen-</span><span class="line">tesque ullamcorper metus sed lorem ultrices tristique. Quisque</span><span class="line">vitae massa luctus ligula congue aliquam. In sagittis, velit ut malesua-</span><span class="line">da feugiat, quam diam bibendum sem, vel tempor lectus est quis</span><span class="line">quam. Nam laoreet purus ut sollicitudin semper. <span class="more">More</span></span></p>
  </div>
</article>

<article class="post" style="top:820px">
  <div class="post-photo" role="img" aria-label="Climbers gathered at the foot of large boulders" style="background:linear-gradient(170deg,#d8d4cc 0%,#a08c78 50%,#6d5d50 100%)"></div>
  <div class="post-body">
    <h2 class="post-title"><span class="line">Pellentesque cursus euismod erat vel blandit.</span><span class="line">Quisque sed dolor iaculis sem sodales congue ut</span></h2>
    <div class="post-meta"><span>2 May, 2017</span><span>● 28 Comments</span><span>♥ 18 Likes</span><span>&lt; Share</span></div>
    <p class="post-excerpt"><span class="line">Mauris sed nibh congue, commodo lorem a, vehicula nulla. Pellen-</span><span class="line">tesque ullamcorper metus sed lorem ultrices tristique. Quisque</span><span class="line">vitae massa luctus ligula congue aliquam. In sagittis, velit ut malesua-</span><span class="line">da feugiat, quam diam bibendum sem, vel tempor lectus est quis</span><span class="line">quam. Nam laoreet purus ut sollicitudin semper. <span class="more">More</span></span></p>
  </div>
</article>

<article class="post" style="top:1002px">
  <div class="post-photo" role="img" aria-label="Hiker crossing a rope suspension bridge in the forest" style="background:linear-gradient(170deg,#6e5a3c 0%,#3f4a3a 55%,#2a3438 100%)"></div>
  <div class="post-body">
    <h2 class="post-title"><span class="line">Pellentesque cursus euismod erat vel blandit.</span><span class="line">Quisque sed dolor iaculis sem sodales congue ut</span></h2>
    <div class="post-meta"><span>2 May, 2017</span><span>● 28 Comments</span><span>♥ 18 Likes</span><span>&lt; Share</span></div>
    <p class="post-excerpt"><span class="line">Mauris sed nibh congue, commodo lorem a, vehicula nulla. Pellen-</span><span class="line">tesque ullamcorper metus sed lorem ultrices tristique. Quisque</span><span class="line">vitae massa luctus ligula congue aliquam. In sagittis, velit ut malesua-</span><span class="line">da feugiat, quam diam bibendum sem, vel tempor lectus est quis</span><span class="line">quam. Nam laoreet purus ut sollicitudin semper. <span class="more">More</span></span></p>
  </div>
</article>

<div class="search" style="top:274px"><span>Search</span>
  <svg width="8" height="8" viewBox="0 0 8 8"><circle cx="3.3" cy="3.3" r="2.5" stroke="#999" fill="none"/><path d="M5.2 5.2L7.5 7.5" stroke="#999"/></svg>
</div>

<aside class="widget" style="top:310px;height:282px">
  <h3 class="widget-title">Popular Post</h3>
  <ul class="widget-list">
    <li><div class="thumb" role="img" aria-label="Grid of app tiles" style="background:linear-gradient(135deg,#2f5fb0,#6d8fd0)"></div><p><span class="line">Cras nulla eros, pellentesque</span><span class="line">non dapibus eget, vehicula</span><span class="line">vehicula sem.</span></p></li>
    <li><div class="thumb" role="img" aria-label="Team meeting" style="background:linear-gradient(135deg,#c9ccd0,#6f7378)"></div><p><span class="line">Cras nulla eros, pellentesque</span><span class="line">non dapibus eget, vehicula</span><span class="line">vehicula sem.</span></p></li>
    <li><div class="thumb" role="img" aria-label="Hands planning on a table" style="background:linear-gradient(135deg,#d8c9a8,#7a6a50)"></div><p><span class="line">Cras nulla eros, pellentesque</span><span class="line">non dapibus eget, vehicula</span><span class="line">vehicula sem.</span></p></li>
    <li><div class="thumb" role="img" aria-label="Notebook and charts" style="background:linear-gradient(135deg,#f0e2c8,#b0835a)"></div><p><span class="line">Cras nulla eros, pellentesque</span><span class="line">non dapibus eget, vehicula</span><span class="line">vehicula sem.</span></p></li>
    <li><div class="thumb" role="img" aria-label="App tiles on a screen" style="background:linear-gradient(135deg,#d84a6a,#4a6ad0)"></div><p><span class="line">Cras nulla eros, pellentesque</span><span class="line">non dapibus eget, vehicula</span><span class="line">vehicula sem.</span></p></li>
  </ul>
</aside>

<aside class="widget" style="top:602px;height:328px">
  <h3 class="widget-title">Videos</h3>
  <ul class="widget-list">
    <li><div class="thumb" role="img" aria-label="Video still" style="background:linear-gradient(135deg,#4a3a30,#1f1a18)"><svg class="play" width="14" height="14" viewBox="0 0 14 14"><circle cx="7" cy="7" r="6" fill="#fff"/><path d="M5.5 4.5v5l4-2.5z" fill="#333"/></svg></div><p><span class="line">Cras nulla eros, pellentesque</span><span class="line">non dapibus eget, vehicula</span><span class="line">vehicula sem.</span></p></li>
    <li><div class="thumb" role="img" aria-label="Video still" style="background:linear-gradient(135deg,#8a5a3a,#3a2a22)"><svg class="play" width="14" height="14" viewBox="0 0 14 14"><circle cx="7" cy="7" r="6" fill="#fff"/><path d="M5.5 4.5v5l4-2.5z" fill="#333"/></svg></div><p><span class="line">Cras nulla eros, pellentesque</span><span class="line">non dapibus eget, vehicula</span><span class="line">vehicula sem.</span></p></li>
    <li><div class="thumb" role="img" aria-label="Video still" style="background:linear-gradient(135deg,#5a6a4a,#2a3020)"><svg class="play" width="14" height="14" viewBox="0 0 14 14"><circle cx="7" cy="7" r="6" fill="#fff"/><path d="M5.5 4.5v5l4-2.5z" fill="#333"/></svg></div><p><span class="line">Cras nulla eros, pellentesque</span><span class="line">non dapibus eget, vehicula</span><span class="line">vehicula sem.</span></p></li>
    <li><div class="thumb" role="img" aria-label="Video still" style="background:linear-gradient(135deg,#a06a3a,#4a2a1a)"><svg class="play" width="14" height="14" viewBox="0 0 14 14"><circle cx="7" cy="7" r="6" fill="#fff"/><path d="M5.5 4.5v5l4-2.5z" fill="#333"/></svg></div><p><span class="line">Cras nulla eros, pellentesque</span><span class="line">non dapibus eget, vehicula</span><span class="line">vehicula sem.</span></p></li>
    <li><div class="thumb" role="img" aria-label="Video still" style="background:linear-gradient(135deg,#7a6a50,#3a3228)"><svg class="play" width="14" height="14" viewBox="0 0 14 14"><circle cx="7" cy="7" r="6" fill="#fff"/><path d="M5.5 4.5v5l4-2.5z" fill="#333"/></svg></div><p><span class="line">Cras nulla eros, pellentesque</span><span class="line">non dapibus eget, vehicula</span><span class="line">vehicula sem.</span></p></li>
    <li><div class="thumb" role="img" aria-label="Video still" style="background:linear-gradient(135deg,#6a4a2a,#1a1410)"><svg class="play" width="14" height="14" viewBox="0 0 14 14"><circle cx="7" cy="7" r="6" fill="#fff"/><path d="M5.5 4.5v5l4-2.5z" fill="#333"/></svg></div><p><span class="line">Cras nulla eros, pellentesque</span><span class="line">non dapibus eget, vehicula</span><span class="line">vehicula sem.</span></p></li>
  </ul>
</aside>

<h3 class="newsletter-title">Newsletter Subscribe</h3>
<div class="newsletter-field" style="top:964px"><span>Email Address</span>
  <svg width="8" height="6" viewBox="0 0 8 6"><rect width="8" height="6" fill="#999"/><path d="M0 0l4 3 4-3" stroke="#fff" fill="none" stroke-width=".8"/></svg>
</div>

<div class="corner">M2</div>
</body>
</html>
```